Corporate Business Card

Very professional, Modern, Not to busy, include phone address email, website
(253) 617-4930, 18761 52nd Avenue S, Kent, WA 98047, martin@plumlinegroup.com, varkoworks.com

Target Market(s)

Manufacturing

Industry/Entity Type

Aero, machining, manufacturing, Off road racing

Contact Information for Business Card

Phone, address email, website

```html
<!DOCTYPE html>
<html lang="en">
<head>
<meta charset="utf-8">
<title>Varko Works – Business Card</title>
<link href="https://fonts.googleapis.com/css2?family=Montserrat:wght@500;700&display=swap" rel="stylesheet">
<style>
  :root {
    --navy: #173a78;
    --red: #d22229;
    --ink: #1b1b1b;
    --card: #ffffff;
    --backdrop: #242725;
  }
  * { margin: 0; padding: 0; box-sizing: border-box; }
  html, body { width: 1200px; height: 910px; overflow: hidden; }
  body {
    background: var(--backdrop);
    font-family: "Montserrat", sans-serif;
    position: relative;
  }
  .card {
    position: absolute;
    width: 700px;
    height: 400px;
    background: var(--card);
    border-radius: 22px;
    overflow: hidden;
  }
  .card--front { left: 110px; top: 40px; }
  .card--back { left: 390px; top: 475px; }

  .brand {
    position: absolute;
    display: flex;
    align-items: center;
    gap: 14px;
  }
  .brand__mark {
    width: 22px;
    height: 22px;
    background: var(--red);
  }
  .brand__name {
    font-weight: 700;
    color: var(--navy);
    letter-spacing: 0.5px;
    white-space: nowrap;
  }
  .card--front .brand { left: 50%; top: 50%; transform: translate(-50%, -50%); }
  .card--front .brand__name { font-size: 56px; }
  .card--back .brand { right: 50px; top: 58px; }
  .card--back .brand__mark { width: 16px; height: 16px; }
  .card--back .brand__name { font-size: 38px; }

  .address {
    position: absolute;
    left: 62px;
    top: 132px;
    font-weight: 500;
    font-size: 17px;
    line-height: 1.35;
    color: var(--ink);
  }
  .contacts {
    position: absolute;
    left: 62px;
    top: 215px;
    list-style: none;
    font-weight: 500;
    font-size: 17px;
    color: var(--ink);
  }
  .contacts li {
    display: flex;
    align-items: center;
    gap: 12px;
    height: 28px;
  }
  .contacts svg { width: 18px; height: 18px; fill: var(--red); flex: none; }

  .bands { position: absolute; left: 0; top: 0; }
  .site-tag {
    position: absolute;
    right: 34px;
    bottom: 42px;
    color: #fff;
    font-weight: 500;
    font-size: 16px;
  }
</style>
</head>
<body>

  <section class="card card--front">
    <div class="brand">
      <span class="brand__mark"></span>
      <span class="brand__name">Varko Works</span>
    </div>
  </section>

  <section class="card card--back">
    <div class="brand">
      <span class="brand__mark"></span>
      <span class="brand__name">Varko Works</span>
    </div>

    <p class="address">18761 52nd Avenue S<br>Kent, WA 98047</p>

    <ul class="contacts">
      <li>
        <svg viewBox="0 0 24 24" aria-hidden="true"><path d="M6.6 10.8a15.1 15.1 0 0 0 6.6 6.6l2.2-2.2a1 1 0 0 1 1-.25 11.4 11.4 0 0 0 3.6.57 1 1 0 0 1 1 1V20a1 1 0 0 1-1 1A17 17 0 0 1 3 4a1 1 0 0 1 1-1h3.5a1 1 0 0 1 1 1c0 1.25.2 2.45.57 3.57a1 1 0 0 1-.25 1z"/></svg>
        (253) 617-4930
      </li>
      <li>
        <svg viewBox="0 0 24 24" aria-hidden="true"><path d="M2 5h20v14H2z M3.5 6.5 12 13l8.5-6.5" stroke="#fff" stroke-width="1.4"/></svg>
        martin@plumlinegroup.com
      </li>
      <li>
        <svg viewBox="0 0 24 24" aria-hidden="true"><circle cx="12" cy="12" r="10"/><path d="M2 12h20M12 2c3 3 3 17 0 20M12 2c-3 3-3 17 0 20" stroke="#fff" stroke-width="1.3" fill="none"/></svg>
        www.varkoworks.com
      </li>
    </ul>

    <svg class="bands" width="700" height="400" viewBox="0 0 700 400" aria-hidden="true">
      <polygon points="0,355 453,355 451,362 0,362" fill="var(--navy)"/>
      <polygon points="0,370 448,370 440,400 0,400" fill="var(--red)"/>
      <polygon points="478,300 700,300 700,400 450,400" fill="var(--navy)"/>
    </svg>
    <span class="site-tag">www.varkoworks.com</span>
  </section>

</body>
</html>
```